Im want a website LIKE VRX's and FleetHollow.com's with product payment options like Trenzo's

I need a website LIKE VRX with a header made EXACTLY LIKE THAT OF FLEETHOLLOWS .

The front page photo should be like that of FLEETHOLLOW's webpage as well.

The name of the website will be called "M.K. (Caldera Key)".

We will be targeting ALL MARKETS in a small town in central Panama and charging businesses "listing fees" like a phone book does but also providing informational blogs, news, and other interesting activities.

THIS IS A MULTI PAGE WEBSITE

THIS IS WHERE VRX's website meets Brivelle/FleetHollow.

Once the layout is built I will tweak and modify, add information, and upload items for sale.

Here is a list of specific categories that should be listed out above the front page header image/search bar

-- Home -- News -- Travel -- Activities -- Shop & Dine -- Store -- More... --

These categories should be spread across the bottom of the page in three sections:

WHATS SO GREAT ABOUT (Caldera Key),
HAND PICKED TOURS
ACTIVITIES etc.

Also lets use www.Trenzo.example 's
"HOT DESTINATIONS"
"BEAT THE BEST PRICES IN BOQUETE"
"OCTOBERS INSIDER PICKS"
"TOP DESTINATIONS"
and spread them in four sections side-by-side near the bottom of the page.

Overall I would like to see the finished product to be something LIKE VRX's and FleetHollows.

WE NEED ONLINE PAYMENT OPTIONS LIKE BRIVELLE'S WEBSITE HAS

This will be a desktop website but should be very mobile friendly as well.

-rodmund

P.S. Good luck!

If it isn't already too late to change the website name, the name of the website should be "Caldera Key". Added Friday, October 9, 2015

What do you guys think the budget should be to win this? Added Saturday, October 10, 2015

www.palmorra.example is the most amazing simple site. Whoever can make me a replica with my specifications will win immediately!!!! Added Sunday, October 18, 2015

OMG www.palmorra.example is the bomb!So simple and elegant. Whoever can make me an EXACT REPLICA OF WWW.PALMORRA.EXAMPLE as my site with the specifications mentioned in my brief will take home the $825.00 immediately! Good luck amigos! Added Sunday, October 18, 2015

Does anybody know how to add recurring monthly billing options on this website? Added Sunday, October 18, 2015

ALL MARKETS

Product

Coded - Design and coding required

5+ page

• Coinvey payment options.
• I must be able to add and remove photos/text and video from the HTML files in the page.
• Be creative my friends, and may the odds be forever in your favor!
• I added some photos of a good layout for our page below.

```html
<!DOCTYPE html>
<html lang="en">
<head>
<meta charset="utf-8">
<title>Caldera Key — Gallery</title>
<link href="https://fonts.googleapis.com/css2?family=Oswald:wght@400;500&family=Open+Sans:wght@400;600;700&display=swap" rel="stylesheet">
<style>
:root{
  --teal:#1aa3b8;
  --teal-dark:#12869a;
  --ink:#1d2124;
  --nav-bg:#23282c;
  --footer-bg:#262b2f;
  --footer-deep:#1b1f22;
  --text:#6b6f73;
  --heading:#3a3f44;
  --rule:#d9dcdf;
  --light:#f4f5f6;
  --card-blue:#3a8fcc;
  --card-red:#d9503f;
  --muted:#9aa0a6;
}
*{box-sizing:border-box;margin:0;padding:0}
html,body{width:1200px;height:2248px;overflow:hidden}
body{background:#fff;font-family:"Open Sans",Arial,sans-serif;color:var(--text);position:relative}

.site-header{position:absolute;top:0;left:0;width:1200px;height:100px;background:linear-gradient(90deg,#1c2226 0%,#2a3136 50%,#1c2226 100%)}
.topbar{position:absolute;top:8px;right:152px;display:flex;gap:26px;font-size:12px;color:#c7cdd2}
.topbar span{display:flex;align-items:center;gap:6px}
.brand{position:absolute;left:152px;top:46px;font-family:"Oswald",sans-serif;font-size:30px;font-weight:400;color:var(--teal);letter-spacing:.5px}
.main-nav{position:absolute;right:152px;top:40px;display:flex;height:44px}
.main-nav a{display:flex;align-items:center;padding:0 15px;font-family:"Oswald",sans-serif;font-size:14px;color:#fff;text-decoration:none;letter-spacing:.5px}
.main-nav a.active{background:var(--teal)}

.page-title{position:absolute;top:100px;left:0;width:1200px;height:92px;background:linear-gradient(90deg,#0f7d8e 0%,#1aa3b8 45%,#17909f 100%)}
.page-title h1{position:absolute;left:152px;top:22px;font-family:"Oswald",sans-serif;font-weight:400;font-size:34px;color:#fff}

.gallery-item{position:absolute;left:152px;width:896px;height:246px}
.gallery-photo{position:absolute;left:0;top:0;width:448px;height:246px}
.gallery-body{position:absolute;left:456px;top:0;width:440px}
.gallery-body h2{font-family:"Oswald",sans-serif;font-weight:400;font-size:32px;color:var(--heading);line-height:36px;padding-bottom:6px;border-bottom:2px solid var(--rule)}
.gallery-body p{margin-top:10px;font-size:11.5px;line-height:15.5px;color:var(--text)}
.btn-more{display:inline-block;margin-top:14px;background:var(--teal);color:#fff;font-family:"Oswald",sans-serif;font-size:12px;padding:6px 14px;letter-spacing:.5px}

.tweet-band{position:absolute;top:1600px;left:0;width:1200px;height:112px;background:var(--teal)}
.tweet-icon{position:absolute;left:152px;top:34px}
.tweet-text{position:absolute;left:210px;top:30px;width:720px;font-size:12.5px;line-height:18px;color:#fff}
.tweet-text small{display:block;color:#d6f1f5;font-size:11px}
.tweet-arrows{position:absolute;left:990px;top:42px;display:flex;gap:4px}
.tweet-arrows span{width:24px;height:24px;background:#fff;display:flex;align-items:center;justify-content:center}

.site-footer{position:absolute;top:1712px;left:0;width:1200px;height:488px;background:var(--footer-bg)}
.footer-about{position:absolute;left:152px;top:40px;width:270px}
.footer-about .brand-foot{font-family:"Oswald",sans-serif;font-size:28px;color:var(--teal)}
.footer-about p{margin-top:14px;font-size:11.5px;line-height:17px;color:var(--muted)}
.partners{display:flex;gap:12px;margin-top:22px}
.partners span{width:72px;height:42px;border:2px solid #6d7378;border-radius:21px}

.deals{position:absolute;left:464px;top:40px;width:270px}
.deals h3{font-family:"Oswald",sans-serif;font-weight:400;font-size:20px;color:var(--teal);letter-spacing:.5px}
.deal{display:flex;gap:14px;margin-top:22px}
.deal-thumb{width:72px;height:62px;flex:none}
.deal h4{font-family:"Oswald",sans-serif;font-weight:400;font-size:16px;color:#fff}
.deal .meta{margin-top:6px;font-size:11px;color:var(--muted);display:flex;gap:12px}

.offer{position:absolute;left:760px;width:288px;height:186px;padding:30px 24px;color:#fff;text-align:right}
.offer.blue{top:36px;background:var(--card-blue)}
.offer.red{top:244px;background:var(--card-red)}
.offer .pct{font-family:"Oswald",sans-serif;font-size:44px;line-height:48px}
.offer .pct small{font-size:24px}
.offer .place{font-family:"Oswald",sans-serif;font-size:20px;margin-top:8px}
.offer .book{display:inline-block;margin-top:12px;border:1px solid #fff;font-size:11px;padding:4px 12px;letter-spacing:.5px}
.offer-icon{position:absolute;left:24px;top:30px}

.copyright{position:absolute;top:2200px;left:0;width:1200px;height:48px;background:var(--footer-deep);text-align:center;line-height:48px;font-size:11.5px;color:var(--muted)}
</style>
</head>
<body>

<header class="site-header">
  <div class="topbar">
    <span><svg width="12" height="10" viewBox="0 0 12 10"><rect x="0.5" y="0.5" width="11" height="9" fill="none" stroke="#c7cdd2"/><path d="M1 1l5 4 5-4" fill="none" stroke="#c7cdd2"/></svg>hello@calderakey.example</span>
    <span><svg width="10" height="12" viewBox="0 0 10 12"><path d="M2 0h3l1 3-2 1.5c.6 1.6 1.6 2.6 3 3.2L8.5 6 11 7v3c-5 1-10-4-9-10z" fill="#c7cdd2"/></svg>0800-555-0142</span>
  </div>
  <div class="brand">Caldera Key</div>
  <nav class="main-nav">
    <a>HOME</a><a class="active">GALLERY</a><a>PACKAGE</a><a>LOCATIONS</a><a>BLOG</a><a>SHORTCODES</a><a>CONTACT</a>
  </nav>
</header>

<section class="page-title"><h1>Gallery</h1></section>

<article class="gallery-item" style="top:248px">
  <div class="gallery-photo" role="img" aria-label="Photo of a misty harbour with boats on calm water" style="background:linear-gradient(160deg,#d8dde0 0%,#a9b4ba 55%,#7d8b93 100%)"></div>
  <div class="gallery-body">
    <h2>PHOTO 1</h2>
    <p>Lorem Ipsum is simply dummy text of the printing and typesetting industry. Lorem Ipsum has been the industry's standard dummy text ever since the 1500s, when an unknown printer took a galley of type and scrambled it to make a type specimen book. It has survived not only five centuries, but also the leap into electronic typesetting, remaining essentially unchanged. It was popularised in the 1960s with the release of Pressmark sheets containing.</p>
    <span class="btn-more">READ MORE</span>
  </div>
</article>

<article class="gallery-item" style="top:514px">
  <div class="gallery-photo" role="img" aria-label="Photo of an ornate stone fountain in a city square" style="background:linear-gradient(170deg,#b9a58a 0%,#8c7863 50%,#5c6f78 100%)"></div>
  <div class="gallery-body">
    <h2>PHOTO 2</h2>
    <p>Lorem Ipsum is simply dummy text of the printing and typesetting industry. Lorem Ipsum has been the industry's standard dummy text ever since the 1500s, when an unknown printer took a galley of type and scrambled it to make a type specimen book. It has survived not only five centuries, but also the leap into electronic typesetting, remaining essentially unchanged. It was popularised in the 1960s with the release of Pressmark sheets containing.</p>
    <span class="btn-more">READ MORE</span>
  </div>
</article>

<article class="gallery-item" style="top:780px">
  <div class="gallery-photo" role="img" aria-label="Photo of a couple running along a sunny beach" style="background:linear-gradient(180deg,#7cc3e4 0%,#a8d8ea 45%,#e9dcc0 75%,#d9c7a3 100%)"></div>
  <div class="gallery-body">
    <h2>PHOTO 3</h2>
    <p>Lorem Ipsum is simply dummy text of the printing and typesetting industry. Lorem Ipsum has been the industry's standard dummy text ever since the 1500s, when an unknown printer took a galley of type and scrambled it to make a type specimen book. It has survived not only five centuries, but also the leap into electronic typesetting, remaining essentially unchanged. It was popularised in the 1960s with the release of Pressmark sheets containing.</p>
    <span class="btn-more">READ MORE</span>
  </div>
</article>

<article class="gallery-item" style="top:1046px">
  <div class="gallery-photo" role="img" aria-label="Photo of a sunset over a rocky coastline" style="background:linear-gradient(180deg,#2f4a7a 0%,#d9823a 40%,#f1b64f 55%,#3f5f7d 80%,#27394f 100%)"></div>
  <div class="gallery-body">
    <h2>PHOTO 4</h2>
    <p>Lorem Ipsum is simply dummy text of the printing and typesetting industry. Lorem Ipsum has been the industry's standard dummy text ever since the 1500s, when an unknown printer took a galley of type and scrambled it to make a type specimen book. It has survived not only five centuries, but also the leap into electronic typesetting, remaining essentially unchanged. It was popularised in the 1960s with the release of Pressmark sheets containing.</p>
    <span class="btn-more">READ MORE</span>
  </div>
</article>

<article class="gallery-item" style="top:1312px">
  <div class="gallery-photo" role="img" aria-label="Photo of a canal with gondolas at dusk" style="background:linear-gradient(180deg,#e8b27a 0%,#c98a5e 40%,#4e6a7c 75%,#2f4656 100%)"></div>
  <div class="gallery-body">
    <h2>PHOTO 5</h2>
    <p>Lorem Ipsum is simply dummy text of the printing and typesetting industry. Lorem Ipsum has been the industry's standard dummy text ever since the 1500s, when an unknown printer took a galley of type and scrambled it to make a type specimen book. It has survived not only five centuries, but also the leap into electronic typesetting, remaining essentially unchanged. It was popularised in the 1960s with the release of Pressmark sheets containing.</p>
    <span class="btn-more">READ MORE</span>
  </div>
</article>

<section class="tweet-band">
  <svg class="tweet-icon" width="36" height="36" viewBox="0 0 36 36"><circle cx="18" cy="18" r="17" fill="#fff"/></svg>
  <p class="tweet-text">RT @calderakey: "In this season we travel more and enjoy every sunny day, join our island tour and see the best beaches" — http://t.co/ckey4<small>256 days ago</small></p>
  <div class="tweet-arrows">
    <span><svg width="8" height="10" viewBox="0 0 8 10"><path d="M6 1L2 5l4 4" fill="none" stroke="#1aa3b8" stroke-width="2"/></svg></span>
    <span><svg width="8" height="10" viewBox="0 0 8 10"><path d="M2 1l4 4-4 4" fill="none" stroke="#1aa3b8" stroke-width="2"/></svg></span>
  </div>
</section>

<footer class="site-footer">
  <div class="footer-about">
    <div class="brand-foot">Caldera Key</div>
    <p>Caldera Key collects island guides, tours and local listings in one place. Find activities, book trips, browse shops and dining, and plan every day of your stay with trusted local help.</p>
    <div class="partners"><span></span><span></span><span></span></div>
  </div>

  <div class="deals">
    <h3>LAST MINUTE DEALS</h3>
    <div class="deal">
      <div class="deal-thumb" role="img" aria-label="Thumbnail of a city skyline" style="background:linear-gradient(160deg,#c9a77e,#6d7f8c)"></div>
      <div><h4>Rome, Milan, Madrid</h4><div class="meta"><span>$ 1,250</span><span>7 days</span></div></div>
    </div>
    <div class="deal">
      <div class="deal-thumb" role="img" aria-label="Thumbnail of an old city street" style="background:linear-gradient(160deg,#d7b98f,#8a6d55)"></div>
      <div><h4>Rome City Tour</h4><div class="meta"><span>$ 480</span><span>3 days</span></div></div>
    </div>
    <div class="deal">
      <div class="deal-thumb" role="img" aria-label="Thumbnail of a bay bridge at sunset" style="background:linear-gradient(160deg,#e59a5a,#5a6f8a)"></div>
      <div><h4>San Francisco</h4><div class="meta"><span>$ 920</span><span>5 days</span></div></div>
    </div>
    <div class="deal">
      <div class="deal-thumb" role="img" aria-label="Thumbnail of a savanna landscape" style="background:linear-gradient(160deg,#c6b36a,#6f7a45)"></div>
      <div><h4>Wild Life Tour</h4><div class="meta"><span>$ 1,640</span><span>9 days</span></div></div>
    </div>
  </div>

  <div class="offer blue">
    <svg class="offer-icon" width="34" height="34" viewBox="0 0 34 34"><circle cx="17" cy="17" r="15" fill="none" stroke="#fff" stroke-width="2"/><path d="M11 17l4 4 8-9" fill="none" stroke="#fff" stroke-width="2"/></svg>
    <div class="pct">20% <small>Off</small></div>
    <div class="place">Rome, Milan, Madrid</div>
    <span class="book">BOOK NOW</span>
  </div>
  <div class="offer red">
    <svg class="offer-icon" width="34" height="34" viewBox="0 0 34 34"><circle cx="17" cy="17" r="15" fill="none" stroke="#fff" stroke-width="2"/><path d="M11 17l4 4 8-9" fill="none" stroke="#fff" stroke-width="2"/></svg>
    <div class="pct">20% <small>Off</small></div>
    <div class="place">San Francisco</div>
    <span class="book">BOOK NOW</span>
  </div>
</footer>

<div class="copyright">Copyright © 2015 Caldera Key. All Rights Reserved.</div>

</body>
</html>
```